Professional Services - letterhead / business cards

The company (velmora partners) will provide services to Investment Funds and large investors in Spain. I have recently chosen a logo that I am attaching.

I would like a simple stationary design that i could use as letter head, business cards and "with compliments" cards.

I am not quite sure which color I will mostly use for the logo, in the email signature I will probably lean towards the white background and grey letters. I am attaching my favourite options.

Target Market(s)

Large Multinationals, Investment funds and Law firms

Industry/Entity Type

Business

Requirements
Must have
• my details are:
Luis R. Abadal
Velmora Partners S.L.
Casa de Torrelumbre
Calle de Vientoalto 27
28014 Madrid
T: +34 (91) 387-2265
M: +34 (646) 819-054
e-mail: labadal@velmorapartners.com

```html
<!DOCTYPE html>
<html lang="en">
<head>
<meta charset="utf-8">
<title>Velmora Partners – Business Cards</title>
<link rel="stylesheet" href="https://fonts.googleapis.com/css2?family=Jost:wght@400;500&display=swap">
<style>
  :root {
    --navy: #0f1a7a;
    --white: #ffffff;
    --rule-grey: #b4b6bc;
    --ink-grey: #5a5d66;
    --backdrop: #e9e7e3;
    --card-shadow: rgba(0, 0, 0, 0.18);
  }
  * { margin: 0; padding: 0; box-sizing: border-box; }
  html, body { width: 1200px; height: 588px; overflow: hidden; }
  body {
    background: var(--backdrop);
    font-family: "Jost", "Futura", sans-serif;
    display: flex;
    align-items: center;
    justify-content: center;
    gap: 60px;
  }
  .card {
    width: 480px;
    height: 310px;
    background: var(--white);
    box-shadow: 0 6px 18px var(--card-shadow);
    position: relative;
    overflow: hidden;
  }

  /* Wordmark */
  .wordmark {
    color: var(--navy);
    font-weight: 400;
    font-size: 40px;
    letter-spacing: 0.5px;
    line-height: 1;
    white-space: nowrap;
  }

  /* Front */
  .card-front {
    display: flex;
    flex-direction: column;
    align-items: center;
    justify-content: center;
    gap: 26px;
  }
  .card-front .website {
    color: var(--navy);
    font-size: 12px;
    letter-spacing: 4px;
    font-style: normal;
  }

  /* Back */
  .card-back .details-band {
    height: 178px;
    background: var(--navy);
    color: var(--white);
    text-align: right;
    padding: 28px 26px 0 20px;
  }
  .card-back .accent-rule {
    height: 4px;
    background: var(--rule-grey);
  }
  .card-back .name-line {
    font-size: 17px;
    letter-spacing: 1px;
    text-transform: uppercase;
  }
  .card-back .name-line .company {
    font-size: 12px;
    text-transform: none;
    letter-spacing: 0.3px;
  }
  .card-back .email {
    font-size: 12px;
    margin-top: 4px;
    opacity: 0.9;
  }
  .card-back .phones {
    font-size: 12.5px;
    margin-top: 14px;
    display: flex;
    justify-content: flex-end;
    align-items: center;
    gap: 6px;
  }
  .card-back .phone-tag {
    display: inline-flex;
    align-items: center;
    justify-content: center;
    width: 15px;
    height: 15px;
    border-radius: 50%;
    background: #d6d7dc;
    color: var(--navy);
    font-size: 9px;
    font-weight: 500;
  }
  .card-back .phones .gap { width: 10px; }
  .card-back .address {
    font-size: 12.5px;
    margin-top: 8px;
    font-style: normal;
  }
  .card-back .logo-area {
    height: 128px;
    display: flex;
    align-items: center;
    justify-content: center;
  }
</style>
</head>
<body>
  <section class="card card-front" aria-label="Business card front">
    <div class="wordmark">velmora partners</div>
    <address class="website">www.velmorapartners.com</address>
  </section>

  <section class="card card-back" aria-label="Business card back">
    <div class="details-band">
      <p class="name-line">Luis R. Abadal, <span class="company">Velmora Partners S.L.</span></p>
      <p class="email">labadal@velmorapartners.com</p>
      <p class="phones">
        <span class="phone-tag">P</span><span>+34 (91) 387-2265</span>
        <span class="gap"></span>
        <span class="phone-tag">C</span><span>+34 (646) 819-054</span>
      </p>
      <address class="address">Casa de Torrelumbre, Calle de Vientoalto 27, 28014 Madrid</address>
    </div>
    <div class="accent-rule"></div>
    <div class="logo-area">
      <div class="wordmark">velmora partners</div>
    </div>
  </section>
</body>
</html>
```